Wireless Internet Service Provider website design

We need a Internet Service Provider website that show the packages that we offer as well as the functionality where customers have the option of clicking on the various packages and be linked to a page where they can sign up for our services.
We need about 10-15 pages.
A. Integrated online store.
B. Live chat.
C. Social media page
My old website. Brightlinkradio.nyc

Example: http://plumcrestnet.com/services/residential/ Added Tuesday, June 7, 2016

Target Market(s)

Residential and small businesses

Industry/Entity Type

Internet

Coding

Coded - Design and coding required

Number of Pages Required

5+ page

Font styles to use
Serif
Sans Serif
Script

Colors
3176b5
85cae6
ffffff

Requirements
Must have
• Online store and live chat, drop down details on pricing from current website
Nice to have
• great design, functional website,

```html
<!DOCTYPE html>
<html lang="en">
<head>
<meta charset="utf-8">
<title>Brightlink Radio — Wireless Internet</title>
<link href="https://fonts.googleapis.com/css2?family=Open+Sans:ital,wght@0,400;0,600;1,400&family=Raleway:wght@400;500;600&display=swap" rel="stylesheet">
<style>
:root{
  --brand:#3176b5;
  --brand-dark:#1c5f9e;
  --navy:#0f2f52;
  --navy-deep:#0a2240;
  --cyan:#24b4d4;
  --cyan-soft:#85cae6;
  --ink:#333a40;
  --muted:#8a9096;
  --line:#dcdfe2;
  --grey-head:#a6a6a6;
  --white:#ffffff;
}
*{box-sizing:border-box;margin:0;padding:0}
html,body{width:1200px;height:2782px;overflow:hidden;background:var(--white)}
body{font-family:"Open Sans",Arial,sans-serif;color:var(--ink);position:relative}
.abs{position:absolute}
.head-font{font-family:"Raleway",Arial,sans-serif}

/* header */
.site-header{position:absolute;left:0;top:0;width:1200px;height:100px;background:var(--white)}
.brand-name{left:116px;top:30px;font-family:"Raleway",sans-serif;font-weight:600;font-size:30px;color:var(--navy);display:flex;align-items:center;gap:10px}
.brand-name .mark{width:26px;height:26px;border-radius:50%;background:var(--cyan)}
.brand-name small{font-size:11px;font-weight:600;margin-left:-6px;margin-top:10px}
.top-contact{right:95px;top:16px;font-size:14px;display:flex;gap:22px;color:var(--ink);font-weight:600}
.top-contact span{display:flex;align-items:center;gap:6px}
.main-nav{right:95px;top:55px;display:flex;gap:36px;font-family:"Raleway",sans-serif;font-size:14px;color:#6b7177;letter-spacing:.3px}
.main-nav .active{color:var(--brand)}

/* hero */
.hero{left:0;top:100px;width:1200px;height:478px;background:linear-gradient(100deg,#eef0f1 0%,#dfe2e3 35%,#c9b3a0 52%,#d8d4cf 65%,#f2f2f2 100%)}
.hero-title{left:127px;top:158px;font-family:"Raleway",sans-serif;font-size:33px;font-weight:500;line-height:46px;letter-spacing:.5px}
.hero-title .l1{color:var(--brand-dark)}
.hero-title .l2{color:var(--cyan)}
.btn-buy{left:127px;top:258px;width:152px;height:46px;background:var(--cyan);color:var(--white);font-family:"Raleway",sans-serif;font-size:17px;font-weight:500;display:flex;align-items:center;justify-content:center}
.dots{left:563px;top:434px;display:flex;gap:6px}
.dots i{width:17px;height:17px;border-radius:50%;background:var(--white);display:block;opacity:.9}

/* welcome */
.welcome{left:0;top:578px;width:1200px;height:329px}
.section-dot{left:581px;width:38px;height:38px;border-radius:50%;background:var(--cyan)}
.section-title{width:1200px;text-align:center;font-family:"Raleway",sans-serif;font-size:23px;color:#2a2f34;letter-spacing:.4px}
.welcome-text{left:172px;top:128px;width:856px;text-align:center;font-size:12px;line-height:24px;color:var(--muted)}
.btn-small{background:var(--brand);color:var(--white);font-size:11px;font-weight:600;display:flex;align-items:center;justify-content:center;border-radius:2px}

/* services */
.services{left:0;top:907px;width:1200px;height:359px;background:linear-gradient(180deg,#27b6d6,#1eafcf)}
.service{width:360px;text-align:center;color:var(--white)}
.service .ring{width:116px;height:116px;border:2px solid var(--white);border-radius:50%;margin:0 auto;display:flex;align-items:center;justify-content:center}
.service h3{font-family:"Raleway",sans-serif;font-weight:500;font-size:18px;margin-top:26px}
.service p{font-size:13px;line-height:24px;color:#d9f3fa;margin-top:10px}
.service .outline{width:110px;height:34px;border:1.5px solid var(--white);margin:20px auto 0;font-size:11px;font-weight:600;display:flex;align-items:center;justify-content:center}

/* pricing */
.pricing{left:0;top:1266px;width:1200px;height:477px}
.plan{top:112px;width:222px;height:307px;background:var(--white);border:1px solid var(--line);text-align:center}
.plan .plan-head{height:40px;background:var(--grey-head);color:var(--white);font-family:"Raleway",sans-serif;font-size:17px;display:flex;align-items:center;justify-content:center}
.plan .price{margin-top:14px;color:var(--brand);font-size:44px;font-weight:400;line-height:50px}
.plan .price sup{font-size:20px;vertical-align:top;position:relative;top:6px;margin-right:4px}
.plan .price small{font-size:22px}
.plan ul{list-style:none;font-size:12px;color:#555;margin-top:8px}
.plan li{padding:4px 0;border-bottom:1px solid #ededed;width:170px;margin:0 auto;line-height:16px}
.plan li:last-child{border:none}
.plan .try{position:absolute;left:19px;bottom:14px;width:184px;height:38px;background:var(--brand-dark);color:var(--white);font-family:"Raleway",sans-serif;font-size:15px;display:flex;align-items:center;justify-content:center}
.plan.featured{top:99px;height:328px;width:240px;box-shadow:0 2px 8px rgba(0,0,0,.15)}
.plan.featured .plan-head{height:46px;background:var(--brand-dark);font-size:19px}
.plan.featured .try{left:20px;width:200px;height:40px}

/* testimonials */
.testimonials{left:0;top:1743px;width:1200px;height:342px;background:linear-gradient(90deg,#4a3e3a,#6d5a52 30%,#3f3532 55%,#7a6259 80%,#3c3230)}
.testimonials h2{top:38px;width:1200px;text-align:center;color:var(--white);font-family:"Raleway",sans-serif;font-weight:400;font-size:29px}
.quote{top:100px;width:309px;height:159px;background:rgba(40,40,40,.72);border:2px solid #d8d8d8;padding:20px 22px}
.quote p{font-size:11.5px;font-style:italic;line-height:20px;color:var(--white)}
.quote .who{font-size:12px;color:var(--cyan);margin-top:10px}
.avatar{right:16px;bottom:-22px;width:74px;height:84px}

/* features */
.features{left:0;top:2085px;width:1200px;height:380px}
.features h2{left:113px;top:20px;font-family:"Raleway",sans-serif;font-weight:400;font-size:27px;line-height:42px;color:#2a2f34}
.features .lead{left:113px;top:146px;width:620px;font-size:11.5px;line-height:20px;color:var(--muted)}
.perk{top:230px;display:flex;align-items:center;gap:14px;color:var(--cyan);font-size:17px;line-height:22px}
.perk .ic{width:56px;height:56px;border-radius:50%;background:var(--cyan);display:flex;align-items:center;justify-content:center}
.social-box{left:768px;top:2133px;width:300px;height:310px;border:1px solid var(--line);box-shadow:0 1px 4px rgba(0,0,0,.1)}
.social-box .bar{height:46px;background:#f3f3f3;border-bottom:1px solid var(--line);color:var(--brand-dark);font-size:16px;padding:12px 22px}
.page-card{left:22px;top:60px;display:flex;gap:14px}
.page-card .sq{width:70px;height:62px;border:1px solid var(--line)}
.page-card b{display:block;color:var(--brand);font-weight:400;font-size:13px}
.page-card .like{display:inline-block;margin-top:4px;width:38px;height:14px;background:var(--brand)}
.page-card span{display:block;font-size:10px;color:#444;margin-top:2px}
.fans{left:22px;top:140px;display:grid;grid-template-columns:repeat(5,46px);gap:10px}
.fans i{width:46px;height:46px;display:block;background:linear-gradient(135deg,#c9b4a4,#8a7466)}
.plugin{left:22px;top:277px;font-size:10px;color:#555;display:flex;align-items:center;gap:6px}
.plugin i{width:14px;height:14px;background:var(--brand);display:block}

/* footer */
.site-footer{left:0;top:2465px;width:1200px;height:257px;background:linear-gradient(180deg,#123a63,#0c2a4b);color:var(--white)}
.f-col{top:48px}
.f-col h4{font-family:"Raleway",sans-serif;font-weight:400;font-size:17px;margin-bottom:12px}
.f-col li{list-style:none;font-size:12px;line-height:22px;color:#e3ecf5}
.f-col p{font-size:12px;line-height:22px;color:#e3ecf5}
.email-field{margin-top:10px;width:222px;height:28px;background:#eceff2;color:#888;font-size:10px;display:flex;align-items:center;padding-left:28px}
.subscribe{margin-top:10px;width:98px;height:30px;background:var(--cyan);font-size:12px;font-weight:600;display:flex;align-items:center;justify-content:center}
.live-chat{left:570px;top:192px;width:122px;height:34px;background:var(--cyan);font-size:15px;display:flex;align-items:center;justify-content:center;gap:6px;border-radius:2px}
.socials{display:flex;gap:8px;margin-top:14px}
.socials i{width:30px;height:30px;border:1.5px solid var(--white);border-radius:50%;display:block}
.copyright{left:0;top:2722px;width:1200px;height:60px;background:var(--navy-deep);color:#9fb0c2;font-size:11px;display:flex;align-items:center;justify-content:center}
</style>
</head>
<body>

<header class="site-header">
  <div class="abs brand-name"><span class="mark"></span>Brightlink Radio<small>LLC</small></div>
  <div class="abs top-contact">
    <span><svg width="14" height="14" viewBox="0 0 24 24"><path fill="#3176b5" d="M6.6 10.8a15.1 15.1 0 0 0 6.6 6.6l2.2-2.2c.3-.3.7-.4 1-.2 1.1.4 2.3.6 3.6.6.6 0 1 .4 1 1V20c0 .6-.4 1-1 1A17 17 0 0 1 3 4c0-.6.4-1 1-1h3.5c.6 0 1 .4 1 1 0 1.3.2 2.5.6 3.6.1.3 0 .7-.2 1z"/></svg>(866)-555-0142</span>
    <span><svg width="16" height="14" viewBox="0 0 24 20"><path fill="#3176b5" d="M0 1h4l3 11h12l3-8H8" stroke="#3176b5" stroke-width="2" fill-opacity="0"/><circle cx="9" cy="17" r="2" fill="#3176b5"/><circle cx="18" cy="17" r="2" fill="#3176b5"/></svg>Shopping Cart</span>
  </div>
  <nav class="abs main-nav">
    <span class="active">HOME</span><span>WHY BRIGHTLINK</span><span>PLAN &amp; PACKAGES</span><span>GALLERY</span><span>CONTACT</span>
  </nav>
</header>

<section class="abs hero" role="img" aria-label="Photo of a smiling man using a laptop on a sofa">
  <div class="abs hero-title"><div class="l1">LOCALLY OWN . RELIABLE</div><div class="l2">SUPER FAST INTERNET</div></div>
  <div class="abs btn-buy">BUY PLAN</div>
  <div class="abs dots"><i></i><i></i><i></i><i></i></div>
</section>

<section class="abs welcome">
  <div class="abs section-dot" style="top:22px"></div>
  <h2 class="abs section-title" style="top:84px">WELCOME TO BRIGHTLINK RADIO</h2>
  <p class="abs welcome-text">Brightlink Radio is a highly reputable company, which is aiming at providing high quality internet access and phone services to a market that is continually growing. We are dedicated to filling the digital gap that has been created in the middle and lowe. When shopping for internet access, people usually look for what is reliable, fast and affordable. This description fits Brightlink Radio LLC the best. Customers who have subscribed to our services are enjoying some of the fastest speeds to be provided by</p>
  <div class="abs btn-small" style="left:545px;top:243px;width:111px;height:34px">READ MORE</div>
</section>

<section class="abs services">
  <div class="abs service" style="left:93px;top:56px">
    <div class="ring"><svg width="60" height="56" viewBox="0 0 60 56" fill="none" stroke="#fff" stroke-width="2.5"><rect x="6" y="4" width="16" height="12"/><rect x="38" y="4" width="16" height="12"/><path d="M14 16v10h32V16M30 26v14M6 46h48"/><circle cx="8" cy="46" r="3"/><circle cx="52" cy="46" r="3"/><circle cx="30" cy="46" r="3"/></svg></div>
    <h3>Residential Internet Access</h3>
    <p>Brightlink's VOIP home phone solutions<br>offer you a reliable, portable</p>
    <div class="outline">READ MORE</div>
  </div>
  <div class="abs service" style="left:428px;top:56px">
    <div class="ring"><svg width="60" height="60" viewBox="0 0 60 60" fill="none" stroke="#fff" stroke-width="2.5"><rect x="8" y="6" width="26" height="46" rx="4"/><path d="M16 46h10"/><circle cx="40" cy="32" r="14"/><path d="M26 32h28M40 18c-6 8-6 20 0 28M40 18c6 8 6 20 0 28"/></svg></div>
    <h3>Business Internet Access</h3>
    <p>Brightlink's VOIP home phone solutions<br>offer you a reliable, portable</p>
    <div class="outline">READ MORE</div>
  </div>
  <div class="abs service" style="left:760px;top:56px">
    <div class="ring"><svg width="62" height="62" viewBox="0 0 62 62"><circle cx="31" cy="31" r="26" fill="#fff"/><path d="M10 24c14-6 28 8 42 2M14 44c12-10 24 2 36-8M31 5c-10 14-10 38 0 52" stroke="#22b2d2" stroke-width="3" fill="none"/></svg></div>
    <h3>Unlimited Internet Usage</h3>
    <p>Brightlink's VOIP home phone solutions<br>offer you a reliable, portable</p>
    <div class="outline">READ MORE</div>
  </div>
</section>

<section class="abs pricing">
  <div class="abs section-dot" style="top:16px"></div>
  <h2 class="abs section-title" style="top:60px">OUR PRICING</h2>
  <div class="abs plan" style="left:156px"><div class="plan-head">Brightlink Simplicity</div><div class="price"><sup>$</sup>39<small>.99</small></div><ul><li>Includes:</li><li>Free smart router</li><li>Free internet protection</li><li>Unlimited Brightlink Wi-Fi access</li></ul><div class="try">TRY IT NOW</div></div>
  <div class="abs plan" style="left:377px"><div class="plan-head">Brightlink Value Pack</div><div class="price"><sup>$</sup>45<small>.95</small></div><ul><li>Includes:</li><li>Free smart router</li><li>Free internet protection</li><li>Unlimited Brightlink Wi-Fi access</li></ul><div class="try">TRY IT NOW</div></div>
  <div class="abs plan" style="left:598px"><div class="plan-head">Brightlink Super Pack</div><div class="price"><sup>$</sup>69<small>.99</small></div><ul><li>Includes:</li><li>Free smart router</li><li>Free internet protection</li><li>Unlimited Brightlink Wi-Fi access</li></ul><div class="try">TRY IT NOW</div></div>
  <div class="abs plan featured" style="left:816px"><div class="plan-head">Brightlink Speed</div><div class="price"><sup>$</sup>89<small>.99</small></div><ul><li>Includes:</li><li>Free smart router</li><li>Free internet protection</li><li>Unlimited Brightlink Wi-Fi access</li></ul><div class="try">TRY IT NOW</div></div>
</section>

<section class="abs testimonials" role="img" aria-label="Dimmed photo background of happy customers">
  <h2 class="abs">Testimonials</h2>
  <div class="abs quote" style="left:116px"><p>"Thanks for your great service. I love my internet and your quick response to my questions and concerns. I would definitely refer Brightlink to my friends and family. Keep up the good work."</p><div class="who">Mark Dalton</div>
    <svg class="abs avatar" viewBox="0 0 74 84" role="img" aria-label="Customer portrait"><polygon points="37,2 72,22 72,62 37,82 2,62 2,22" fill="#b9a596" stroke="#fff" stroke-width="3"/></svg></div>
  <div class="abs quote" style="left:442px"><p>"By far the best customer service I have ever received from an Internet service provider. Brightlink stands above the rest, thanks for the rapid resolution to my problem."</p><div class="who">Peter Nolan</div>
    <svg class="abs avatar" viewBox="0 0 74 84" role="img" aria-label="Customer portrait"><polygon points="37,2 72,22 72,62 37,82 2,62 2,22" fill="#c8b8aa" stroke="#fff" stroke-width="3"/></svg></div>
  <div class="abs quote" style="left:770px"><p>"Brightlink is the best internet servicer provider in Brooklyn, finally a better option to internet service. My family and I are enjoying faster downloads streaming movies, thank you for your fast</p><div class="who">Lena Sharp</div>
    <svg class="abs avatar" viewBox="0 0 74 84" role="img" aria-label="Customer portrait"><polygon points="37,2 72,22 72,62 37,82 2,62 2,22" fill="#a89484" stroke="#fff" stroke-width="3"/></svg></div>
</section>

<section class="abs features">
  <h2 class="abs">Fast download &amp; upload speeds at<br>an affordable price</h2>
  <p class="abs lead">When choosing among the best high speed internet providers, there are several other factors that should be taken into consideration besides just the available download speeds. Upload speeds are important as well, though they probably are not as crucial as download speeds.</p>
  <div class="abs perk" style="left:107px"><span class="ic"><svg width="28" height="26" viewBox="0 0 28 26" fill="#fff"><path d="M3 2h22a2 2 0 0 1 2 2v13a2 2 0 0 1-2 2H12l-6 5v-5H3a2 2 0 0 1-2-2V4a2 2 0 0 1 2-2z"/></svg></span>Customer<br>Support center</div>
  <div class="abs perk" style="left:312px"><span class="ic"><svg width="26" height="26" viewBox="0 0 26 26"><circle cx="13" cy="13" r="9" fill="none" stroke="#fff" stroke-width="5" stroke-dasharray="4 3"/><circle cx="13" cy="13" r="4" fill="#fff"/></svg></span>Equipment<br>Options</div>
  <div class="abs perk" style="left:507px"><span class="ic"><svg width="28" height="28" viewBox="0 0 24 24"><path d="M12 2l3 6.5 7 .8-5.2 4.8 1.5 7L12 17.6 5.7 21l1.5-7L2 9.3l7-.8z" fill="none" stroke="#fff" stroke-width="2"/></svg></span>Customer<br>Guarantee</div>
</section>

<aside class="abs social-box">
  <div class="bar">Follow us on our social page</div>
  <div class="abs page-card"><div class="sq"></div><div><b>Brightlink Radio</b><i class="like"></i><span>71 people like Brightlink Radio</span></div></div>
  <div class="abs fans" role="img" aria-label="Grid of follower profile photos"><i></i><i></i><i></i><i></i><i></i><i></i><i></i><i></i><i></i><i></i></div>
  <div class="abs plugin"><i></i>Social page plugin</div>
</aside>

<footer class="abs site-footer">
  <div class="abs f-col" style="left:124px"><h4>Quick Links</h4><ul><li>Refer a Friend</li><li>Free Internet for life</li><li>Terms &amp; Conditions</li><li>Privacy Policy</li><li>Site Map</li></ul></div>
  <div class="abs f-col" style="left:304px"><h4>Resources</h4><ul><li>Wireless Internet Access Agreement</li><li>Brightlink Internet Access</li><li>Customer Support Center</li><li>Catalog</li></ul></div>
  <div class="abs f-col" style="left:569px"><h4>Newsletter Sign Up</h4><p>Please Sign up here for latest deals</p><div class="email-field">Enter your email</div><div class="subscribe">Subscribe</div></div>
  <div class="abs live-chat"><svg width="18" height="16" viewBox="0 0 28 26" fill="#fff"><path d="M3 2h22a2 2 0 0 1 2 2v13a2 2 0 0 1-2 2H12l-6 5v-5H3a2 2 0 0 1-2-2V4a2 2 0 0 1 2-2z"/></svg>Live Chat</div>
  <div class="abs f-col" style="left:849px"><h4>Contact Us</h4><p>240 Harbor Lane<br>3rd Fl Brooklyn, NY 11201</p><p style="font-size:14px">&#9742; 866-555-0142</p><p>&#9993; support@brightlinkradio.nyc</p><div class="socials"><i></i><i></i><i></i><i></i></div></div>
</footer>
<div class="abs copyright">© 2016 Company Name&nbsp; All right reserved &nbsp;Term of Use</div>

</body>
</html>
```